Give Gold Kite an Online Presence!

Gold Kite Property Maintenance is an Australian Owned property maintenance company who needs a stand out online presence.

GK maintains many buildings and sites and wants to appeal to a corporate professional market with their brand new website. GK is essentially a handyman service offering all maintenance services to home owners, office managers, real estate agents and strata managers.

The Website:
We need a corporate website that appeals to our broader customer base (property owners, property managers, office managers) the copy is being written by a professional so use filler text for now.

Things that we want:
Home page that sets us apart and appeals to the corporate and residential market. The home page needs to not focus on either the residential or commercial market. The home page should focus on our logo and branding. We have a logo already and it is attached to the brief, please use it and try to consider the colour pallette that goes with it. Whilst we want the site to appear strong and manly it is important to remember that 95% of our customers are female so we need the site to be appealing to women. Women need to believe that we are strong, dependable and trustworthy.
We'd like a quote page and potentially also the ability to get a quote from the home page (please don't put it in if it ruins the overall feel of the home page)
An "about us" page
A contact us page
A blog that's built in (we don't want to link to an external blog)
(overall we'd expect to have 6 or 7 pages total)

The site will also need coding - we expect this to be done in a separate project but need you to consider a few things about the coding side of things.

It needs to be iPhone and iPad compatible.

We'd like you to suggest the best CMS that you would use or if you would suggest not using a CMS please let us know with your submissions.

Target Market(s)

Property owners, office managers and property managers who need maintenance on buildings (So all of them)

Industry/Entity Type

Property Maintenance

Requirements
Must have
• Our Logo
Home page
About Us
Residential
Commercial
Real Estate/Strata
Contact Us/Quote
Blog
Nice to have
• Quote form included in home page
Movement on the home page at least
Should not have
• other logos, too much colour
NO FLASH

```html
<!DOCTYPE html>
<html lang="en">
<head>
<meta charset="utf-8">
<title>Gold Kite Property Maintenance</title>
<link rel="stylesheet" href="https://fonts.googleapis.com/css2?family=Signika:wght@300;400;600&family=Rye&family=Open+Sans:wght@400;600&display=swap">
<style>
:root{
  --gold:#d98f00;
  --gold-dark:#c27f00;
  --ink:#222;
  --header:#262424;
  --header-top:#1c1b1b;
  --text:#777;
  --link:#0a6ab4;
  --white:#fff;
  --panel-border:#dcdcdc;
}
*{box-sizing:border-box;margin:0;padding:0}
html,body{width:1200px;height:1200px;overflow:hidden;background:var(--white);font-family:"Open Sans",Arial,sans-serif}
.page{position:relative;width:1200px;height:1200px}
.topbar{position:absolute;left:0;top:0;width:1200px;height:12px;background:var(--gold)}
.header{position:absolute;left:0;top:12px;width:1200px;height:91px;background:linear-gradient(var(--header-top),#2e2c2c)}
.brand{position:absolute;left:146px;top:30px;display:flex;align-items:center;gap:7px;font-family:"Signika",sans-serif;font-weight:600;font-size:17px;color:var(--gold)}
.brand-mark{width:12px;height:12px;background:var(--gold)}
.nav{position:absolute;left:333px;top:0;display:flex;height:91px}
.nav a{display:block;padding:0 15.5px;height:91px;font-family:"Signika",sans-serif;font-weight:300;font-size:16px;color:#eee;text-decoration:none;line-height:108px}
.nav a.active{background:var(--gold);color:var(--white);padding:0 13px}
.hero{position:absolute;left:129px;top:113px;width:942px;height:418px;border:1px solid var(--panel-border);background:var(--white);box-shadow:0 14px 14px -10px rgba(0,0,0,.25)}
.hero-photo{position:absolute;left:6px;top:6px;width:625px;height:406px;background:linear-gradient(100deg,#d9d2bd 0%,#c7b98e 35%,#b94a3a 60%,#5d6fa5 100%)}
.dots{position:absolute;left:27px;bottom:14px;display:flex;gap:9px}
.dots span{width:12px;height:12px;border-radius:50%;background:#333}
.dots span.on{background:var(--gold)}
.quote{position:absolute;left:641px;top:6px;width:295px;height:406px;background:var(--gold)}
.quote h2{position:absolute;left:20px;top:9px;font-family:"Rye",serif;font-weight:400;font-size:29px;color:#fbe3b0;letter-spacing:2px}
.quote label{position:absolute;left:24px;font-family:"Signika",sans-serif;font-weight:300;font-size:13px;color:#222}
.field{position:absolute;left:15px;width:264px;height:34px;background:var(--white);border-radius:8px}
.quote-btn{position:absolute;left:83px;top:364px;width:126px;height:32px;border-radius:6px;background:linear-gradient(#3a3a3a,#111);color:var(--white);font-family:"Signika",sans-serif;font-size:17px;text-align:center;line-height:31px}
.worker{position:absolute;left:992px;top:347px;width:86px;height:178px;border-radius:30px 30px 4px 4px;background:linear-gradient(#7a5a3a,#8a8f9c)}
.welcome{position:absolute;left:139px;top:558px;font-family:"Signika",sans-serif;font-weight:300;font-size:17px;color:var(--ink)}
.heading{position:absolute;left:139px;top:595px;font-family:"Signika",sans-serif;font-weight:600;font-size:15px;color:var(--gold)}
.lead{position:absolute;left:139px;top:621px;width:614px;font-size:11.6px;line-height:24px;color:var(--text);text-align:justify}
.feature-frame{position:absolute;left:137px;top:757px;width:277px;height:227px;border:1px solid var(--panel-border);box-shadow:0 12px 12px -9px rgba(0,0,0,.2)}
.feature-photo{position:absolute;left:4px;top:4px;width:267px;height:217px;background:linear-gradient(90deg,#e6e1da,#d98a4a 40%,#c07a3a 70%,#e3ddd6)}
.feature-text{position:absolute;left:428px;top:758px;width:319px;font-size:11.6px;line-height:24px;color:var(--text);text-align:justify;hyphens:auto}
.more{position:absolute;font-family:"Signika",sans-serif;font-weight:600;font-size:11px;color:var(--gold)}
.testimonial{position:absolute;left:138px;top:1013px;width:603px;height:86px;border-radius:8px;background:var(--gold);color:var(--white)}
.testimonial h3{position:absolute;left:14px;top:8px;font-family:"Signika",sans-serif;font-weight:300;font-size:24px}
.testimonial .meta{position:absolute;right:18px;top:9px;font-size:12px}
.testimonial p{position:absolute;left:16px;top:41px;width:575px;font-family:Arial,sans-serif;font-size:12.4px;line-height:18px}
.support{position:absolute;left:769px;top:572px;width:299px;height:200px;border:1px solid var(--panel-border);box-shadow:0 12px 12px -9px rgba(0,0,0,.2)}
.support-inner{position:absolute;left:4px;top:4px;width:289px;height:190px;background:var(--white)}
.support-photo{position:absolute;left:72px;top:0;width:217px;height:190px;background:linear-gradient(90deg,rgba(255,255,255,0),#e8c9a8 45%,#c49a6a 70%,#2d2a2a 100%)}
.support h3{position:absolute;left:17px;top:16px;font-family:"Signika",sans-serif;font-weight:300;font-size:22px;line-height:28px;color:var(--gold)}
.support .phone{position:absolute;left:19px;top:110px;font-family:Arial,sans-serif;font-size:14px;color:#111}
.blog-title{position:absolute;left:787px;top:801px;font-family:"Signika",sans-serif;font-weight:600;font-size:15px;color:var(--gold)}
.post{position:absolute;left:790px;width:260px;height:70px}
.post-thumb{position:absolute;left:0;top:0;width:92px;height:64px;border:1px solid #ddd;padding:3px;background:var(--white);box-shadow:0 3px 4px rgba(0,0,0,.15)}
.post-thumb div{width:100%;height:100%}
.post h4{position:absolute;left:100px;top:-3px;font-family:Arial,sans-serif;font-weight:400;font-size:13px;color:var(--link)}
.post p{position:absolute;left:103px;top:15px;width:155px;font-family:Arial,sans-serif;font-size:11.6px;line-height:17.5px;color:#555}
.divider{position:absolute;left:790px;width:257px;border-top:1px dotted #666}
.footer{position:absolute;left:0;top:1123px;width:1200px;height:77px;background:var(--header)}
.footer-nav{position:absolute;left:141px;top:17px;display:flex;gap:28px;font-family:"Signika",sans-serif;font-weight:300;font-size:14px;color:#ddd}
.copyright{position:absolute;left:140px;top:54px;font-family:"Open Sans",sans-serif;font-size:12px;color:var(--white)}
.follow{position:absolute;left:970px;top:18px;font-family:"Open Sans",sans-serif;font-weight:600;font-size:12px;color:var(--white)}
.social{position:absolute;left:962px;top:42px;display:flex;gap:4px}
.social span{width:26px;height:26px;border-radius:3px;background:#5f8fbf}
</style>
</head>
<body>
<div class="page">
  <div class="topbar"></div>
  <header class="header">
    <div class="brand"><span class="brand-mark"></span>Gold Kite</div>
    <nav class="nav">
      <a class="active">Home</a><a>About Us</a><a>Residential</a><a>Commercial</a><a>Real Estate/Strata</a><a>Contact Us/Quote</a><a>Blog</a>
    </nav>
  </header>

  <section class="hero">
    <div class="hero-photo" role="img" aria-label="Slideshow photo of a smiling tradeswoman in a red headscarf hanging a hook with a hammer">
      <div class="dots"><span></span><span></span><span></span><span class="on"></span></div>
    </div>
    <form class="quote">
      <h2>QUICK QUOTE</h2>
      <label style="top:69px">Name</label><div class="field" style="top:91px"></div>
      <label style="top:131px">Email</label><div class="field" style="top:152px"></div>
      <label style="top:192px">Phone</label><div class="field" style="top:213px"></div>
      <label style="top:253px">Message</label><div class="field" style="top:274px;height:74px"></div>
      <div class="quote-btn">Get a Quote</div>
    </form>
  </section>
  <div class="worker" role="img" aria-label="Cut-out photo of a handyman with a drill and tool belt"></div>

  <h1 class="welcome">Welcome to Our Website</h1>
  <h2 class="heading">HEADING</h2>
  <p class="lead">Lorem ipsum dolor sit amet, consectetur adipisicing elit, sed do eiusmod tempor incididunt ut labore et dolore magna aliqua. Ut enim ad minim veniam, quis nostrud exercitation ullamco laboris nisi ut aliquip ex ea commodo consequat. Duis aute irure dolor in reprehenderit in voluptate velit esse cillum Sed ut perspiciatis unde omnis iste natus error sit voluptatem accusantium doloremque laudantium, totam rem aperiam, eaque ipsa quae ab illo inventore veritatis et quasi architecto beatae vitae dicta sunt explicabo.</p>

  <div class="feature-frame"><div class="feature-photo" role="img" aria-label="Photo of a worker in a tool belt holding a small model house"></div></div>
  <p class="feature-text" lang="en">Lorem ipsum dolor sit amet, consectetur adipisicing elit, sed do eiusmod tempor incididunt ut labore et dolore magna aliqua. Ut enim ad minim veniam, quis nostrud exer&shy;citation ullamco laboris nisi ut aliquip ex ea commodo con&shy;sequat. Duis aute irure dolor in reprehenderit in voluptate velit esse cillum Sed ut perspiciatis unde omnis iste natus error sit voluptatem accusantium doloremque laudantium, totam rem aperiam, eaque</p>
  <span class="more" style="left:651px;top:957px">&gt;&gt; READ MORE...</span>

  <section class="testimonial">
    <h3>Testimonial</h3>
    <span class="meta">2 days ago - lee</span>
    <p>Sed ut perspiciatis unde omnis iste natus error sit voluptatem accusantium doloremque laudantium, totam rem aperiam, eaque ipsa quae ab illo inventore vequia</p>
  </section>

  <aside class="support">
    <div class="support-inner">
      <div class="support-photo" role="img" aria-label="Photo of a smiling support agent wearing a headset"></div>
      <h3>Support<br>you<br>any time</h3>
      <span class="phone">02 5550 0147</span>
    </div>
  </aside>

  <h2 class="blog-title">BLOG POST</h2>
  <article class="post" style="top:831px">
    <div class="post-thumb"><div role="img" aria-label="Thumbnail of a red fruit" style="background:radial-gradient(circle at 45% 45%,#e23a1a,#5a0a05 70%,#111)"></div></div>
    <h4>This is a sample Post 1</h4>
    <p>Lorem ipsum dolor sit amet, consectetuer adipiscing elit, sed diam nonummy nibh...</p>
  </article>
  <div class="divider" style="top:911px"></div>
  <article class="post" style="top:927px">
    <div class="post-thumb"><div role="img" aria-label="Black and white thumbnail of roses" style="background:radial-gradient(circle,#bbb,#333 60%,#111)"></div></div>
    <h4>This is a sample Post 1</h4>
    <p>Lorem ipsum dolor sit amet, consectetuer adipiscing elit, sed diam nonummy nibh...</p>
  </article>
  <div class="divider" style="top:1006px"></div>
  <article class="post" style="top:1023px">
    <div class="post-thumb"><div role="img" aria-label="Thumbnail of a strawberry" style="background:radial-gradient(circle at 45% 55%,#c8151a 25%,#f0eeee 45%,#fff)"></div></div>
    <h4>This is a sample Post 1</h4>
    <p>Lorem ipsum dolor sit amet, consectetuer adipiscing elit, sed diam nonummy nibh...</p>
  </article>
  <span class="more" style="left:955px;top:1102px">&gt;&gt; READ MORE...</span>

  <footer class="footer">
    <div class="footer-nav"><span>Home</span><span>About Us</span><span>Residential</span><span>Commercial</span><span>Real Estate/Strata</span><span>Contact Us/Quote</span><span>Blog</span></div>
    <div class="copyright">© 2012.www.gksydneyhandyman.com.au</div>
    <div class="follow">Follow us on :</div>
    <div class="social"><span></span><span></span><span></span></div>
  </footer>
</div>
</body>
</html>
```